Banner for promote service of debit card

We are PagoLume and we need the banners to be posted on the facebook and instagram pages.
We want something to communicate that it is an exclusive debit card full of services.
Low commissions.
Our competitors:
https://www.kelmora.example/it/home.html
https://www.zofe.example/it/
https://www.socialpage.example/ostrevabank/
monadrift
maybe some banner that makes the idea of a convenient debit card that everyone can use.
Girls enjoying card shopping.
Please check also website for slogans and phrases to use
https://www.pagolume.example/
Should show the services.
We must convey that it is a fast, simple card that guarantees privacy.
We need strong banners that attract people as these ban will be sponsored on instagram and facebook
People 18-35 y
Open Bank account. low commissions. Easy to use. No limits. 100% Privacy.
- Written in Italian.

```html
<!DOCTYPE html>
<html lang="it">
<head>
<meta charset="UTF-8">
<title>PagoLume – Una carta per tutti</title>
<link rel="stylesheet" href="https://fonts.googleapis.com/css2?family=Roboto+Condensed:wght@400;700&family=Roboto:wght@400;500;700&display=swap">
<style>
  :root {
    --stage: #2a2b2f;
    --violet-deep: #4a2a86;
    --violet: #7a2f93;
    --magenta: #c23a86;
    --pink-soft: #e0649a;
    --yellow: #f4c21a;
    --yellow-deep: #e2a712;
    --white: #ffffff;
    --ink: #2b1636;
  }
  * { box-sizing: border-box; margin: 0; padding: 0; }
  html, body { width: 1200px; height: 800px; overflow: hidden; }
  body {
    background: var(--stage);
    font-family: "Roboto", Arial, sans-serif;
    display: flex; align-items: center; justify-content: center;
  }
  .banner {
    position: relative;
    width: 600px; height: 720px;
    overflow: hidden;
    background: linear-gradient(160deg, var(--violet-deep) 0%, var(--violet) 40%, var(--magenta) 75%, var(--pink-soft) 100%);
  }
  .banner__shapes { position: absolute; inset: 0; }
  .banner__photo {
    position: absolute; left: 110px; top: 70px; width: 400px; height: 360px;
    border-radius: 40% 40% 20% 20%;
    background: radial-gradient(ellipse at 50% 40%, rgba(240,170,160,.55) 0%, rgba(190,90,140,.45) 45%, rgba(120,50,140,0) 75%);
  }
  .banner__card {
    position: absolute; left: 420px; top: 70px; width: 150px; height: 95px;
    border-radius: 10px;
    transform: rotate(-16deg);
    background: linear-gradient(135deg, #3a3a44 0%, #1c1c22 100%);
    box-shadow: 0 10px 24px rgba(0,0,0,.35);
  }
  .brand {
    position: absolute; left: 32px; top: 34px;
    display: flex; align-items: center; gap: 10px;
  }
  .brand__dot { width: 26px; height: 26px; border-radius: 50%; background: var(--white); }
  .brand__name {
    font-family: "Roboto Condensed", Arial, sans-serif;
    font-weight: 700; font-size: 26px; color: var(--white);
  }
  .offer { position: absolute; left: 40px; top: 400px; width: 500px; }
  .offer__headline {
    font-family: "Roboto Condensed", Arial, sans-serif;
    font-weight: 700; font-size: 46px; line-height: 1.02;
    color: var(--white); text-transform: uppercase;
    text-shadow: 0 2px 6px rgba(0,0,0,.25);
  }
  .offer__copy {
    margin-top: 18px;
    font-size: 17px; line-height: 1.35; color: var(--white);
  }
  .offer__cta {
    display: inline-block; margin-top: 20px;
    padding: 11px 24px; border-radius: 24px;
    background: var(--yellow);
    font-weight: 700; font-size: 17px; color: var(--ink);
  }
</style>
</head>
<body>
  <main class="banner">
    <svg class="banner__shapes" width="600" height="720" viewBox="0 0 600 720" aria-hidden="true">
      <polygon points="600,420 600,720 440,720" fill="var(--yellow)" opacity="0.95"/>
      <polygon points="600,530 600,720 515,720" fill="var(--yellow-deep)"/>
      <polygon points="0,690 0,720 40,720" fill="var(--yellow)"/>
      <polygon points="420,720 600,570 600,605 465,720" fill="rgba(255,255,255,.12)"/>
    </svg>

    <div class="banner__photo" role="img" aria-label="Foto di due ragazze sorridenti che si divertono a fare shopping con la carta"></div>
    <div class="banner__card" role="img" aria-label="Carta di debito PagoLume"></div>

    <div class="brand">
      <span class="brand__dot"></span>
      <span class="brand__name">PagoLume</span>
    </div>

    <section class="offer">
      <h1 class="offer__headline">All in one!<br>Una carta per tutti!</h1>
      <p class="offer__copy">Enjoy your cart!<br>Fai quello che vuoi.<br>Nessun limite.<br>Nessun controllo.</p>
      <span class="offer__cta">Ottieni la tua Carta</span>
    </section>
  </main>
</body>
</html>
```